Roofing company in Toronto, Canada needs a logo design and business card design

We need a business card and logo created for our company. Our company is "KLV Roofing" which provides roofing services for commercial and residential customers. We serve customers in the Greater Toronto Area (in Canada) thus the name KLV.

We want the logo and business card to be a modern design displaying professionalism and quality in the work. We would prefer rounded corners for the business cards but are open to other ideas. The cards should be pleasant and appealing to customers.

Target Market(s)

Commercial and Residential customers

Industry/Entity Type

Roofing

Contact Information for Business Card

Logo Text

KLV Roofing

Requirements
Nice to have
• Colours that are pleasing to the eye but at the same time should stand out from other business cards. If the design can incorporate the name of KLV Roofing and the actual concept of roofing that would be nice.
Should not have
• Do not want the business cards or logo to be childish looking. Need to look professionally designed.

```html
<!DOCTYPE html>
<html lang="en">
<head>
<meta charset="utf-8">
<title>KLV Roofing – Business Card</title>
<link rel="stylesheet" href="https://fonts.googleapis.com/css2?family=Open+Sans:wght@400;600;700&display=swap">
<style>
  :root {
    --brand-red: #b30000;
    --red-deep: #a80000;
    --ink: #1e1e1e;
    --ink-soft: #444;
    --rule: #c8c8c8;
    --paper: #ffffff;
    --stage: #e6e7ea;
  }
  * { box-sizing: border-box; margin: 0; padding: 0; }
  html, body { width: 1200px; height: 864px; overflow: hidden; }
  body {
    background: var(--stage);
    font-family: "Open Sans", Arial, sans-serif;
    position: relative;
  }
  .card {
    position: absolute;
    width: 580px;
    height: 330px;
    border-radius: 14px;
    box-shadow: 0 6px 18px rgba(0,0,0,.18);
    overflow: hidden;
  }
  .card--front {
    left: 150px; top: 60px;
    background: linear-gradient(135deg, var(--brand-red), var(--red-deep));
    display: flex; align-items: center; justify-content: center;
  }
  .card--back {
    left: 470px; top: 470px;
    background: var(--paper);
  }
  .wordmark {
    display: flex; align-items: center; gap: 14px;
    font-weight: 700;
    letter-spacing: 1px;
    line-height: 1;
  }
  .wordmark__square { width: 22px; height: 22px; }
  .card--front .wordmark { color: var(--paper); font-size: 56px; }
  .card--front .wordmark__square { background: var(--paper); }
  .card--back .wordmark {
    position: absolute; right: 50px; top: 60px;
    color: var(--brand-red); font-size: 46px;
  }
  .card--back .wordmark__square { background: var(--brand-red); width: 18px; height: 18px; }
  .holder { position: absolute; left: 40px; top: 100px; }
  .holder__name { color: var(--brand-red); font-size: 21px; font-weight: 600; }
  .holder__role { color: var(--ink-soft); font-size: 13px; }
  .divider {
    position: absolute; left: 40px; right: 40px; top: 160px;
    border-top: 1px solid var(--rule);
  }
  .contacts {
    position: absolute; right: 40px; top: 190px;
    list-style: none; text-align: right;
  }
  .contacts li {
    display: flex; justify-content: flex-end; align-items: center; gap: 10px;
    font-size: 15px; color: var(--ink); line-height: 23px;
  }
  .contacts svg { width: 13px; height: 13px; fill: var(--brand-red); flex: none; }
</style>
</head>
<body>
  <section class="card card--front" aria-label="Card front">
    <div class="wordmark"><span class="wordmark__square"></span>KLV Roofing</div>
  </section>

  <section class="card card--back" aria-label="Card back">
    <div class="wordmark"><span class="wordmark__square"></span>KLV Roofing</div>
    <div class="holder">
      <p class="holder__name">Marcus Bellamy</p>
      <p class="holder__role">Managing Director</p>
    </div>
    <div class="divider"></div>
    <ul class="contacts">
      <li>044-555-0142
        <svg viewBox="0 0 16 16"><path d="M3 1l3 3-2 2c1 2 4 5 6 6l2-2 3 3-2 2C7 15 1 9 1 3z"/></svg></li>
      <li>123-555-0188
        <svg viewBox="0 0 16 16"><rect x="4" y="1" width="8" height="4"/><rect x="1" y="6" width="14" height="9" rx="1"/></svg></li>
      <li>123-555-0196
        <svg viewBox="0 0 16 16"><path d="M4 0h8a1 1 0 011 1v14a1 1 0 01-1 1H4a1 1 0 01-1-1V1a1 1 0 011-1zm1 2v10h6V2z"/></svg></li>
      <li>info@klvroofing.ca
        <svg viewBox="0 0 16 16"><path d="M0 3h16v10H0zM1 4l7 5 7-5z" fill-rule="evenodd"/></svg></li>
      <li>www.klvroofing.ca
        <svg viewBox="0 0 16 16"><path d="M6 10l4-4M7 4l2-2a3 3 0 014 4l-2 2M9 12l-2 2a3 3 0 01-4-4l2-2" stroke="#b30000" stroke-width="2" fill="none"/></svg></li>
    </ul>
  </section>
</body>
</html>
```